Investment company needing business card

We are wanting a business card which looks sharp and easy on the eye. We are thinking of having a business card with the logo embossed on it, to really make it stand out. We will only have a small amount of information of the business card, person's name, position, email address and phone number

Contact Information for Business Card

Danielle Frost
Executive Assistant
+64 21 473 5162
danielf@harwickpartners.co.nz

Requirements
Must have
• Embossed logo
Should not have
• Not to be busy

```html
<!DOCTYPE html>
<html lang="en">
<head>
<meta charset="utf-8">
<title>Harwick Partners – Business Card</title>
<link rel="stylesheet" href="https://fonts.googleapis.com/css2?family=Arimo:wght@400;700&display=swap">
<style>
  :root {
    --backdrop: #141518;
    --card-light: #e5e5e5;
    --card-dark: #0e0e0e;
    --brand-green: #20a466;
    --brand-grey: #5c5c5c;
    --text-grey: #444444;
    --emboss-ink: #060606;
  }
  * { margin: 0; padding: 0; box-sizing: border-box; }
  html, body { width: 1200px; height: 965px; overflow: hidden; }
  body {
    background: var(--backdrop);
    font-family: "Arimo", Arial, sans-serif;
    position: relative;
  }
  .card {
    position: absolute;
    left: 277px;
    width: 648px;
    height: 369px;
    overflow: hidden;
  }
  .card-front { top: 97px; background: var(--card-light); }
  .card-back { top: 504px; background: var(--card-dark); }

  .side-band {
    position: absolute;
    left: 40px;
    top: 0;
    width: 89px;
    height: 100%;
    background: var(--brand-green);
  }
  .side-band-top {
    position: absolute;
    left: 0; top: 0;
    width: 100%;
    height: 125px;
    background: var(--brand-grey);
  }
  .brand-name {
    position: absolute;
    left: 137px;
    top: 72px;
    font-size: 30px;
    font-weight: 700;
    letter-spacing: 0.5px;
    color: var(--brand-green);
    white-space: nowrap;
  }
  .contact-person {
    position: absolute;
    left: 168px;
    top: 226px;
  }
  .person-name {
    font-size: 21px;
    color: var(--brand-green);
    line-height: 1.1;
  }
  .person-role {
    font-size: 16px;
    color: var(--text-grey);
    margin-top: 2px;
  }
  .contact-list {
    list-style: none;
    position: absolute;
    left: 168px;
    top: 295px;
    font-size: 16px;
    color: var(--text-grey);
  }
  .contact-list li {
    display: flex;
    align-items: center;
    gap: 6px;
    height: 19px;
  }
  .contact-icon { width: 12px; height: 12px; flex: none; }

  .back-brand {
    position: absolute;
    left: 0; right: 0;
    top: 160px;
    text-align: center;
    font-size: 36px;
    font-weight: 700;
    letter-spacing: 1px;
    color: var(--emboss-ink);
  }
</style>
</head>
<body>
  <section class="card card-front" aria-label="Business card front">
    <div class="side-band"><div class="side-band-top"></div></div>
    <div class="brand-name">HARWICK PARTNERS</div>
    <div class="contact-person">
      <p class="person-name">DANIELLE FROST</p>
      <p class="person-role">Executive Assistant</p>
    </div>
    <ul class="contact-list">
      <li>
        <svg class="contact-icon" viewBox="0 0 12 12" aria-hidden="true">
          <circle cx="6" cy="6" r="6" fill="var(--brand-green)"/>
          <path d="M4 3.2 L5 4.6 L4.5 5.3 Q5.4 6.8 6.7 7.5 L7.4 7 L8.8 8 L8.1 8.9 Q5.6 8.6 3.2 4.1 Z" fill="#fff"/>
        </svg>
        +64 21 473 5162
      </li>
      <li>
        <svg class="contact-icon" viewBox="0 0 12 12" aria-hidden="true">
          <circle cx="6" cy="6" r="6" fill="var(--brand-green)"/>
          <rect x="3" y="4" width="6" height="4.2" fill="none" stroke="#fff" stroke-width="0.8"/>
          <path d="M3 4 L6 6.4 L9 4" fill="none" stroke="#fff" stroke-width="0.8"/>
        </svg>
        danielf@harwickpartners.co.nz
      </li>
    </ul>
  </section>

  <section class="card card-back" aria-label="Business card back">
    <div class="back-brand">HARWICK PARTNERS</div>
  </section>
</body>
</html>
```